Briloran Clear Springs needs a new business card design (we produce and sell pure bottled water)

We need a clean modern design for our new business cards, We have an existing logo which ultimately cannot be changed, however it could be slighty improved and the colours adjusted. We have this existing logo on all of our bottles, vehicles etc.

Our company slogan is "Pure down to the last drop".
Along with our relevant company information
(Address, phone, website email etc) we will only be using names and not putting position titles for flexibilty.

We are looking for a clean, minimalist modern design.

You can view our website (if need of an update also!) to see our business.

Industry/Entity Type

Business

Contact Information for Business Card

Staff Name : XXXXXX XXXXXX
Address : 9/41 Tavenor St
Halden Rise QLD 4172
Staff Mobile Number : 04XX XXX XXX
Office Phone Number : 07 3918 2457
Staff Email Address : XXXX@brilorancleargo.com.au
Website : www.brilorancleargo.com.au

Font styles to use
Sans Serif

Colors
cee9f5
33a6d7
0492cd
0455a3
3276b5
85abd2
cedeed

Requirements
Must have
• The ability to edit and change the staff members details as we will need to edit for each respective staff member (7 in total)

```html
<!DOCTYPE html>
<html lang="en">
<head>
<meta charset="utf-8">
<title>Briloran Clear Springs – Business Card</title>
<link rel="stylesheet" href="https://fonts.googleapis.com/css2?family=Open+Sans:wght@400;600;700&family=Noto+Serif:ital@0;1&display=swap">
<style>
  :root {
    --page-bg: #eef1f4;
    --card-bg: #ffffff;
    --brand-blue: #3b3aa6;
    --ink: #2a2a2e;
    --ink-soft: #4a4a52;
    --card-shadow: rgba(20, 30, 60, 0.18);
  }
  * { box-sizing: border-box; margin: 0; padding: 0; }
  html, body {
    width: 1200px;
    height: 1200px;
    overflow: hidden;
    background: var(--page-bg);
  }
  .sheet {
    width: 1200px;
    height: 1200px;
    display: flex;
    flex-direction: column;
    align-items: center;
    justify-content: center;
    gap: 70px;
  }
  .card {
    width: 840px;
    height: 480px;
    background: var(--card-bg);
    box-shadow: 0 14px 36px var(--card-shadow);
    position: relative;
  }
  .brand {
    display: flex;
    align-items: center;
    gap: 14px;
  }
  .brand-dot {
    width: 26px;
    height: 26px;
    border-radius: 50%;
    background: var(--brand-blue);
    flex: none;
  }
  .brand-name {
    font-family: "Open Sans", sans-serif;
    font-weight: 700;
    color: var(--brand-blue);
    text-transform: uppercase;
    line-height: 1.05;
    letter-spacing: 0.5px;
  }

  /* Front */
  .card-front .brand {
    position: absolute;
    left: 150px;
    top: 110px;
  }
  .card-front .brand-name { font-size: 40px; }
  .details {
    position: absolute;
    left: 320px;
    top: 225px;
  }
  .staff-name {
    font-family: "Noto Serif", serif;
    font-size: 34px;
    color: var(--brand-blue);
    margin-bottom: 10px;
  }
  .contact-line {
    font-family: "Open Sans", sans-serif;
    font-size: 19px;
    color: var(--ink-soft);
    line-height: 1.6;
  }
  .contact-line.website {
    font-weight: 700;
    font-size: 21px;
    color: var(--ink);
  }

  /* Back */
  .card-back {
    display: flex;
    flex-direction: column;
    align-items: center;
    justify-content: center;
    gap: 40px;
  }
  .card-back .brand-name { font-size: 48px; }
  .card-back .brand-dot { width: 32px; height: 32px; }
  .slogan {
    font-family: "Noto Serif", serif;
    font-style: italic;
    font-size: 28px;
    color: var(--ink);
  }
</style>
</head>
<body>
  <main class="sheet">
    <section class="card card-front" aria-label="Business card front">
      <div class="brand">
        <span class="brand-dot"></span>
        <span class="brand-name">Briloran<br>Clear Springs</span>
      </div>
      <div class="details">
        <p class="staff-name">Marcus Hale</p>
        <p class="contact-line phone">0739182457</p>
        <p class="contact-line email">hello@brilorancleargo.com</p>
        <p class="contact-line website">www.brilorancleargo.com</p>
        <p class="contact-line address">9/41 Tavenor St Halden Rise QLD 4172</p>
      </div>
    </section>

    <section class="card card-back" aria-label="Business card back">
      <div class="brand">
        <span class="brand-dot"></span>
        <span class="brand-name">Briloran<br>Clear Springs</span>
      </div>
      <p class="slogan">“Pure down to the last drop”</p>
    </section>
  </main>
</body>
</html>
```